Automotive eCommerce Business looking for a business card design

Looking for a clean and simple business card design. Our company name is "Brindle Auto" and we are a company specializing in the ecommerce sales of automotive parts, specifically for pick up trucks and large SUVs. Our company colours are red, black, and white.

Feel free to use the logo provided or create a new logo that you seem fit. Looking forward to your creative ideas!

Industry/Entity Type

Automotive

Contact Information for Business Card

We were thinking of a possibly two-sided design featuring just the logo and company name on one side, and personal information on the other side. Single sided designs will be considered as well.

Font styles to use
Serif
Sans Serif
Decorative

Colors
ec1f27
ffffff
000000

Requirements
Must have
• Space for employee's name, title, phone number and email address, along with the company address and website somewhere.

```html
<!DOCTYPE html>
<html lang="en">
<head>
<meta charset="utf-8">
<title>Brindle Auto – Business Card</title>
<link rel="stylesheet" href="https://fonts.googleapis.com/css2?family=Cinzel:wght@500&family=Roboto:wght@400;500;700&family=Roboto+Condensed:wght@700&display=swap">
<style>
  :root {
    --backdrop: #2b2b2b;
    --card-white: #f1f1f1;
    --brand-red: #9b1c21;
    --charcoal: #4a4e4f;
    --ink: #4d4d4d;
    --paper-text: #ffffff;
  }
  * { margin: 0; padding: 0; box-sizing: border-box; }
  html, body { width: 1200px; height: 960px; overflow: hidden; }
  body {
    position: relative;
    background: var(--backdrop);
    font-family: "Roboto", Arial, sans-serif;
  }
  .card {
    position: absolute;
    width: 600px;
    height: 342px;
    overflow: hidden;
    box-shadow: 0 2px 6px rgba(0,0,0,0.5);
  }
  .card-front { left: 314px; top: 113px; background: var(--card-white); }
  .card-back { left: 311px; top: 472px; background: var(--charcoal); }

  .front-wave { position: absolute; inset: 0; }

  .brand-mark {
    position: absolute;
    left: 112px;
    top: 44px;
    width: 62px;
    height: 62px;
    background: var(--brand-red);
  }
  .brand-name {
    position: absolute;
    left: 45px;
    top: 160px;
    width: 196px;
    text-align: center;
    font-family: "Cinzel", Georgia, serif;
    font-weight: 500;
    font-size: 20px;
    color: var(--ink);
    white-space: nowrap;
  }

  .contact-block {
    position: absolute;
    right: 30px;
    top: 114px;
    text-align: right;
    color: var(--paper-text);
  }
  .person-name {
    font-family: "Roboto Condensed", Arial, sans-serif;
    font-weight: 700;
    font-size: 21px;
    line-height: 24px;
    text-transform: uppercase;
  }
  .person-title {
    font-weight: 500;
    font-size: 15px;
    line-height: 20px;
    text-transform: uppercase;
  }
  .address {
    margin-top: 16px;
    font-size: 14px;
    line-height: 18px;
  }
  .contact-list {
    list-style: none;
    margin-top: 10px;
  }
  .contact-list li {
    display: flex;
    justify-content: flex-end;
    align-items: center;
    gap: 6px;
    font-size: 14px;
    line-height: 19.5px;
  }
  .contact-list svg { width: 14px; height: 14px; fill: var(--paper-text); }

  .back-name {
    position: absolute;
    left: 0;
    right: 0;
    top: 140px;
    text-align: center;
    font-family: "Cinzel", Georgia, serif;
    font-weight: 500;
    font-size: 40px;
    color: var(--paper-text);
  }
  .back-web {
    position: absolute;
    left: 0;
    right: 0;
    top: 296px;
    text-align: center;
    font-size: 14px;
    letter-spacing: 5px;
    color: var(--paper-text);
  }
</style>
</head>
<body>

<section class="card card-front">
  <svg class="front-wave" viewBox="0 0 600 342" aria-hidden="true">
    <path d="M0,212 C70,240 150,292 262,262 C380,228 430,52 600,46 L600,56 C445,60 392,238 268,274 C150,306 70,262 0,236 Z" fill="var(--charcoal)"/>
    <path d="M0,242 C70,268 150,312 270,282 C395,248 440,66 600,62 L600,342 L0,342 Z" fill="var(--brand-red)"/>
  </svg>

  <div class="brand-mark"></div>
  <div class="brand-name">Brindle Auto Ltd.</div>

  <div class="contact-block">
    <div class="person-name">Owen Hale</div>
    <div class="person-title">CEO/Founder</div>
    <div class="address">2140 Cedar Ridge Road<br>Fairbanks, Alaska 99701</div>
    <ul class="contact-list">
      <li>555 210 4873
        <svg viewBox="0 0 16 16"><path d="M3.5 1l2.5 3-1.5 1.8c.8 1.9 2.3 3.4 4.2 4.2L10.5 8.5l3 2.5-1.2 2.8c-6-.4-10.2-4.6-10.6-10.6z"/></svg>
      </li>
      <li>555 318 6042
        <svg viewBox="0 0 16 16"><path d="M4.5 0h7v16h-7zM5.8 1.6v11h4.4v-11zM7.3 13.6h1.4v1.2H7.3z" fill-rule="evenodd"/></svg>
      </li>
      <li>555 742 1196
        <svg viewBox="0 0 16 16"><path d="M4 2h8v4H4zM1 6h14v6h-2v-2H3v2H1zM4 11h8v4H4z"/></svg>
      </li>
      <li>owen@brindleauto.com
        <svg viewBox="0 0 16 16"><path d="M1 3.5h14L8 9zM1 5l7 5.5L15 5v8H1z"/></svg>
      </li>
      <li>www.brindleauto.com
        <svg viewBox="0 0 16 16"><path d="M8 1a7 7 0 1 0 0 14A7 7 0 0 0 8 1zm-1 2.2c-.6 1.2-2.6 1.4-2.4 3 .2 1.4 2 1 2.4 2.4.3 1.2-.4 2.4.2 3.6-2.6-.4-4.2-2.6-4-5 .2-2.2 1.8-3.8 3.8-4zm2.2.1c1.8.5 3.4 2.2 3.6 4.2-.8-.4-1.6-1.2-2.6-.6-1 .6.2 2.2-.8 3-.6.4-1.4-.2-1.6-1-.2-1.2 1.2-1.6 1.2-2.8 0-1-1-1.6.2-2.8z"/></svg>
      </li>
    </ul>
  </div>
</section>

<section class="card card-back">
  <div class="back-name">Brindle Auto</div>
  <div class="back-web">www.brindleauto.com</div>
</section>

</body>
</html>
```